Velmora Gems - High end custom Jewelry website

I need a web design for an online custom jewelry company called Velmora Gems. (www.velmoragems-demo.com) this company specializes in high-end custom made engagement rings, wedding bands and jewelry of all kinds (necklaces, earrings, bracelets etc)All our jewelry uses diamonds so there must be a focus on diamonds on every type of jewelry we will be designing off the website.

We are a company located in New York City but our website will
aim to cater to international, national clients and as well as New York city residents.The company low overhead provides diamonds and precious metal at a discounted costs compared to its competitors. Velmora Gems makes unique custom diamond jewelry of a higher quality and at a lower price than carriage trade retail jewellers. (meaning that our company allows our customers to save money on diamond jewelry then they would if they bought from any known store or company)

The website will act as a tool for our customers to create their own jewelry. The way they will do this is by uploading pictures of what they like, they can post any pictures they want (from drawings, to actual copy and pasted pictures from other websites of designs) From these designs we will create a 3D digital image of the jewelry they like and customize it - however they want (colours, size etc) and then give them a quote in price. From the quote they will either approve it and we can have it made for them in 1 weeks time. If they decline it we will try to do whatever it is they want for the design to suit their needs.

We want the website to be simple and user friendly since people will be working on it to create their own individual jewelry pieces. Therefore some useful headings should include:

"Custom Jewellery" or something like "your design" "Custom Design"

a drop heading here should show the following steps into creating the jewelry.

step 1:
upload pictures of the designs you like
step 2:
What is your ring size?
Step 3:
What setting would you like your ring in? platinum, 14k etc..
Step 4:
What is your budget?
Step 5 :
Once you’ve uploaded pictures and give an explanation of what you want then we will contact you by phone or email and proceed to design your ring. Give us your contact info in this step.

Other then that other headings id like to see on the site are:

"Home"
main page with appealing picture which I can later add text to it explaining our company

"About us"
will include a brief section of who we are

"Wedding/engagment"

We are based in New York City and our company offers a one-to-one personal service to our clients ensuring their expectations are well met and, if we can help it, surpassed. We are a personal shopping and diamond supplier to individuals. Custom design is our speciality weather it be wedding ring, engagement ring or anniversary ring we aim to create distinctive designs that both reflect your personality as well as the beauty of the gemstones used in your piece. We use platinum, 14l-18k gold and diamonds to whatever it is that you may desire.
We in our company believe that we are privileged to be a part of one of the biggest events in our customer’s lives, and we pride ourselves on making sure that our customers have the best experience possible. As the diamond is the center piece of every engagement ring, we at VG make sure that our clients find the best diamond possible that is within their budget. Similarly, we work with established jewellery artisans from Belgium to provide the highest possible craftsmanship to a ring design of your choice. We make sure that our rings are made by the true and tried traditional methods focused on quality rather than quantity and of course our diamonds are QRB certified.

Diamonds

A section that explains where our diamonds come from. A heading will drop down here that is a diamond guide, as shown below.
Diamond Guide

An overview of the 4 C’s and different settings, a section for a brief education on diamonds.
Client Experiences

A section where clients share their experiences with Velmora Gems and can post pictures and share stories about their engagement etc.

The colour i would like to see are white and black, white and dark blue or royal blue. I don't think pastel colours will look good with this, maybe accents of purple or something pastel but for the main colours I want to keep it classic and sophisticated since it is a diamond company.

"Sign in | Check out"
where users are able to create a profile and upload their pictures and create their designs..

and a "search section"

or something along these lines or if you can incorporate both:

Exquisite craftsmanship Finest quality diamonds
Will beat any competitors price by twenty to seventy percent guaranteed
Price quotes whitin24 hours

Upload design picture or sketch
Receive price quote within 24hours
Receive and approve free customized design
Receive you jewelry in 1 week or less

Engagment Ring or necklace, earring, etc
Name
EMail
phone
Competitior Link
Budget

The final design should communicate that Velmora Gems is a custom jewelry site that allows individuals to personalize any type of jewellery they want with diamonds - at a fraction of the cost in comparison to any other out there. Our team works very hard to ensure that you will be so involved in the custom order process that there is no chance of something not being made to your requests. Jewelry is made to the highest standard or it does not ship in the first place. In the event a custom order does not suit a customer, we will take returns within 14 days of delivery less a 25% restocking fee.

Target Market(s)

middle class and upper class people ages 25-45

Industry/Entity Type

Digital

Requirements
Must have
• We have the logo now that I will attach BUT if you want to design something else please feel free ! I am open to all designs and ideas.
My logo now is simply a sketch so even if we make it look a bit more professional and classy I would like that, I think I want to keep it simple just black and white and maybe make the diamond shiny if possible. other then black in white I liked the gold and black combination too.. but as I said open to any other creative ideas!

can take pictures of jewelry off this website:
http://www.plinthwaredesigns.example/library/rings.html
Nice to have
• We already have a logo but we would like to see a banner or something that indicated saving money on diamond jewelry without it looking tacky or too cheap..

Also would like to see artistic pictures if you can of jewelry alongside very simple designs of jewelry that the masses like, (anything trendy or appealing to the eye)

cursive or elegant writing could be nice, flash could also be incorporated in the main page..

Should not have
• Nothing to old fashioned, when I mean elegant maybe just the the name of the company in cursive writing (Velmora Gems) but the actual headings and font on the website to be in a widely used font on jewelry websites. Please no hot pink colours or anything neon..
no times new roman font..

```html
<!DOCTYPE html>
<html lang="en">
<head>
<meta charset="utf-8">
<title>Velmora Gems — Custom Diamond Jewellery</title>
<link href="https://fonts.googleapis.com/css2?family=Source+Sans+3:wght@300;400;600&family=Roboto+Condensed:wght@400&display=swap" rel="stylesheet">
<style>
  :root{
    --ink:#111;
    --text:#444;
    --muted:#8a8a8a;
    --line:#dcdcdc;
    --white:#fff;
    --night:#000;
    --panel-edge:#3a3a3a;
    --field:#eeeeee;
    --nav-top:#f7f7f7;
    --nav-bottom:#e2e2e2;
  }
  *{box-sizing:border-box;margin:0;padding:0}
  html,body{width:802px;height:1200px;overflow:hidden;background:var(--white)}
  body{position:relative;font-family:"Source Sans 3",Arial,sans-serif;color:var(--text)}
  .abs{position:absolute}

  /* header */
  .brand{left:301px;top:14px;width:200px;text-align:center}
  .brand-dot{width:24px;height:24px;border:2px solid var(--ink);border-radius:50%;margin:6px auto 10px}
  .brand-name{font-size:22px;font-weight:400;color:var(--ink);letter-spacing:1px}
  .account-links{left:552px;top:12px;font-size:9px;color:var(--muted)}
  .account-links span{margin:0 4px}
  .search{left:574px;top:77px;width:167px;height:22px;border:1px solid #d3d3d3;font-size:8.5px;font-style:italic;color:var(--muted);padding:5px 8px}
  .search svg{position:absolute;right:7px;top:4px}

  .nav{left:0;top:111px;width:802px;height:36px;background:linear-gradient(var(--nav-top),var(--nav-bottom));border-top:1px solid var(--line);display:flex;justify-content:center;align-items:center;font-family:"Roboto Condensed",Arial,sans-serif;font-size:12.5px;color:#333;letter-spacing:.5px}
  .nav a{color:inherit;text-decoration:none;padding:0 14px;border-left:1px solid #aaa;line-height:15px}
  .nav a:first-child{border-left:none}

  /* hero */
  .hero{left:0;top:147px;width:802px;height:300px;background:var(--night);overflow:hidden}
  .hero-media{left:330px;top:0;width:472px;height:300px;
    background:
      radial-gradient(ellipse 40% 20% at 35% 20%,rgba(220,225,235,.28),transparent 70%),
      radial-gradient(ellipse 40% 20% at 75% 22%,rgba(220,225,235,.25),transparent 70%),
      linear-gradient(172deg,transparent 38%,rgba(90,100,150,.45) 47%,rgba(150,110,170,.35) 52%,rgba(60,80,120,.3) 57%,transparent 66%),
      radial-gradient(ellipse 70% 45% at 60% 55%,#30344a 0%,#14151d 55%,#000 100%);
    -webkit-mask-image:linear-gradient(90deg,transparent 0%,#000 22%,#000 92%,transparent 100%);
            mask-image:linear-gradient(90deg,transparent 0%,#000 22%,#000 92%,transparent 100%)}
  .hero-kicker{left:65px;top:78px;font-size:23px;font-weight:300;color:var(--white)}
  .hero-title{left:65px;top:104px;font-size:29px;font-weight:600;color:var(--white);line-height:36px}
  .hero-copy{left:67px;top:128px;width:285px;font-size:9.6px;line-height:17px;color:#e6e6e6;margin-top:17px}
  .dots{left:67px;top:219px;display:flex;gap:3px}
  .dots i{width:9px;height:9px;border-radius:50%;background:#666}
  .dots i.on{background:var(--white)}

  /* intro */
  .intro-title{left:0;top:476px;width:802px;text-align:center;font-size:22.5px;font-weight:400;color:var(--ink)}
  .intro-copy{left:74px;top:509px;width:654px;text-align:center;font-size:10.2px;line-height:16px;color:var(--muted)}
  .showcase{border-radius:50%;width:124px;height:124px;top:568px;border:1px solid #e6e6e6;display:flex;align-items:center;justify-content:center;background:var(--white)}
  .showcase div{width:86px;height:86px;border-radius:50%}
  .divider{left:58px;top:721px;width:686px;height:6px;background:linear-gradient(#f0f0f0,transparent)}

  /* promo panels */
  .promo{left:65px;width:210px;height:117px;background:linear-gradient(#2b2b2b,#111);border:1px solid var(--panel-edge);box-shadow:0 1px 2px rgba(0,0,0,.4);color:var(--white)}
  .promo svg{position:absolute;left:15px;top:20px}
  .promo h3{position:absolute;left:61px;top:16px;font-size:16.5px;font-weight:400;line-height:20px}
  .promo p.sub{position:absolute;left:61px;top:37px;font-size:11.5px;font-weight:300;color:#ddd}
  .promo p.note{position:absolute;left:61px;top:56px;font-size:8.5px;font-weight:300;color:#888}
  .promo .btn{position:absolute;left:61px;top:77px;height:19px;padding:0 10px;background:linear-gradient(#fff,#dcdcdc);border-radius:2px;font-size:9px;font-weight:400;color:#222;line-height:19px}

  .card{top:768px;height:240px;background:var(--white);border:1px solid #e2e2e2;border-top:none;border-radius:0 0 4px 4px;box-shadow:0 2px 2px rgba(0,0,0,.08)}
  .card h2{position:absolute;left:18px;top:17px;font-size:16.5px;font-weight:400;color:#333}
  .blog{left:297px;width:210px}
  .post{position:absolute;left:18px;width:180px;height:44px}
  .post .thumb{position:absolute;left:0;top:0;width:61px;height:42px}
  .post h4{position:absolute;left:71px;top:-1px;font-size:10.5px;font-weight:400;color:#444}
  .post p{position:absolute;left:71px;top:14px;width:105px;font-size:8px;line-height:13px;color:#999}

  .enquiry{left:523px;width:210px;border:1px solid #ddd;background:linear-gradient(#fff,#f4f4f4)}
  .field{position:absolute;left:17px;width:177px;height:22px;background:var(--field);border:1px solid #ddd;border-radius:2px;font-size:8.5px;color:#888;padding:5px 10px}
  .submit{position:absolute;left:118px;top:197px;width:76px;height:23px;background:linear-gradient(#333,#000);color:var(--white);font-size:10px;font-weight:600;text-align:center;line-height:23px;border-radius:2px}

  /* footer */
  .footer{left:0;top:1060px;width:802px;height:140px;background:linear-gradient(#141414,#0a0a0a)}
  .promise{left:60px;top:26px;font-size:11.5px;font-weight:400;line-height:17px;color:#e8e8e8;letter-spacing:.2px}
  .legal{left:60px;top:102px;font-size:9px;color:#999}
  .social{left:639px;top:25px;display:flex;gap:3px}
  .social i{width:22px;height:22px;border-radius:50%;background:var(--white);display:flex;align-items:center;justify-content:center}
  .social i::after{content:"";width:10px;height:10px;border-radius:50%;border:2px solid #1a1a1a}
</style>
</head>
<body>

<header>
  <div class="abs brand">
    <div class="brand-dot"></div>
    <div class="brand-name">Velmora Gems</div>
  </div>
  <nav class="abs account-links">My Account <span>|</span> Log In <span>|</span> My Cart <span>|</span> Support</nav>
  <div class="abs search">Search here..
    <svg width="12" height="12" viewBox="0 0 12 12"><circle cx="5" cy="5" r="3.6" fill="none" stroke="#888" stroke-width="1.6"/><line x1="7.7" y1="7.7" x2="11" y2="11" stroke="#888" stroke-width="1.8"/></svg>
  </div>
</header>

<nav class="abs nav">
  <a href="#">HOME</a><a href="#">LATEST PRODUCTS</a><a href="#">ABOUT US</a><a href="#">SPECIAL</a><a href="#">ORDER NOW</a><a href="#">CONTACT</a>
</nav>

<section class="abs hero">
  <div class="abs hero-media" role="img" aria-label="Four diamond engagement rings reflected on a dark surface"></div>
  <h2 class="abs hero-kicker">Duis tincidunt lectus</h2>
  <h1 class="abs hero-title">Suspendisse vulputate</h1>
  <p class="abs hero-copy">Mauris vel lacus vitae felis vestibulum volutpat. Etiam est nunc, venenatis in, tristique eu, imperdiet ac, nisl. Cum sociis natoque penatibus et magnis dis parturient montes</p>
  <div class="abs dots"><i class="on"></i><i></i><i></i><i></i></div>
</section>

<section>
  <h2 class="abs intro-title">Duis tincidunt lectus quis dui viverra vestibulum</h2>
  <p class="abs intro-copy">Mauris vel lacus vitae felis vestibulum volutpat. Etiam est nunc, venenatis in, tristique eu, imperdiet ac, nisl. Cum sociis natoque penatibus et magnis dis parturient montes, nascetur ridiculus mus. In iaculis facilisis massa. Etiam eu urna. Sed porta.</p>
  <div class="abs showcase" style="left:130px"><div role="img" aria-label="Solitaire diamond ring" style="background:radial-gradient(circle at 45% 35%,#fff 0%,#e6e7ea 35%,#c3c5ca 62%,#fff 72%)"></div></div>
  <div class="abs showcase" style="left:269px"><div role="img" aria-label="Rose gold pearl pendant necklace" style="background:radial-gradient(circle at 50% 55%,#fbf8f4 0%,#efd9cc 30%,#d7a58b 58%,#fff 72%)"></div></div>
  <div class="abs showcase" style="left:413px"><div role="img" aria-label="Sapphire and diamond flower pendant" style="background:radial-gradient(circle at 50% 58%,#1c2466 0%,#3a3f7a 18%,#e2c4b0 40%,#c99a80 58%,#fff 72%)"></div></div>
  <div class="abs showcase" style="left:556px"><div role="img" aria-label="Gold diamond tennis bracelet" style="background:radial-gradient(ellipse 60% 40% at 50% 50%,#fff 0%,#fff 40%,#e9e2c6 62%,#c9bd93 80%,#fff 100%)"></div></div>
  <div class="abs divider"></div>
</section>

<section>
  <div class="abs promo" style="top:767px">
    <svg width="38" height="34" viewBox="0 0 38 34"><path d="M9 2h20l8 10-18 20L1 12z" fill="none" stroke="#fff" stroke-width="3" stroke-linejoin="round"/><path d="M1 12h36M14 2l-4 10 9 20 9-20-4-10" fill="none" stroke="#fff" stroke-width="2"/></svg>
    <h3>Custom Jewellery</h3>
    <p class="sub">Create your own jewellery</p>
    <p class="note">Vivamus porttitor, g, purus nisi</p>
    <span class="btn">CLICK HERE</span>
  </div>
  <div class="abs promo" style="top:890px">
    <svg width="36" height="36" viewBox="0 0 36 36"><circle cx="22" cy="13" r="10" fill="none" stroke="#fff" stroke-width="3.5"/><line x1="15" y1="20" x2="4" y2="32" stroke="#fff" stroke-width="5" stroke-linecap="round"/></svg>
    <h3>Find Jewellery</h3>
    <p class="sub">Find your jewllery now</p>
    <p class="note">Vivamus porttitor, g, purus nisi</p>
    <span class="btn">FIND NOW</span>
  </div>

  <div class="abs card blog">
    <h2>Recent Blog Post</h2>
    <article class="post" style="top:51px">
      <div class="thumb" role="img" aria-label="Loose diamonds" style="background:radial-gradient(circle at 30% 40%,#fff,#d8dbe0 40%,#a9adb5 80%)"></div>
      <h4>Mauris vel lacus vitae</h4>
      <p>Vivamus porttitor, g, purus nisi eleifend libero</p>
    </article>
    <article class="post" style="top:110px">
      <div class="thumb" role="img" aria-label="Diamond rings on black" style="background:radial-gradient(circle at 45% 45%,#9a9ca3,#2a2a2a 45%,#050505 80%)"></div>
      <h4>Etiam est nunc</h4>
      <p>Vivamus porttitor, g, purus nisi eleifend libero</p>
    </article>
    <article class="post" style="top:170px">
      <div class="thumb" role="img" aria-label="Gold diamond bands" style="background:radial-gradient(circle at 55% 55%,#fff6d2,#e6cc76 40%,#b48f3a 85%)"></div>
      <h4>Suspendisse vulputate</h4>
      <p>Vivamus porttitor, g, purus nisi eleifend libero</p>
    </article>
  </div>

  <form class="abs card enquiry" style="top:766px;height:242px;border-top:1px solid #ddd;border-radius:4px">
    <h2>Engagement Ring</h2>
    <div class="field" style="top:51px">First Name</div>
    <div class="field" style="top:80px">Emai address</div>
    <div class="field" style="top:110px">Phone no.</div>
    <div class="field" style="top:139px">Competitor Link</div>
    <div class="field" style="top:168px">Budget</div>
    <div class="submit">SUBMIT</div>
  </form>
</section>

<footer class="abs footer">
  <p class="abs promise">Exquisite craftsmanship Finest quality diamonds<br>Will beat any competitors price by twenty to seventy percent guaranteed<br>Price quotes within 24 hours</p>
  <p class="abs legal">© 2013 Company Name.&nbsp; All right reserved.&nbsp; Term of Use</p>
  <div class="abs social" aria-label="Social links"><i></i><i></i><i></i><i></i></div>
</footer>

</body>
</html>
```